Companybrochure for Consulting & Financing Firm

I need to have a Company Brochure asap for our company. We have a website that describes what we do, but we need also a brochure, that can be sent by PDF of eventually be printed as well.

The brochure should be short but nice and appealing to the customers.

We provide professional management consulting and help our customers to get finance for very diferent projects. Our business has a lot to do with personal relations, but also we are very professional in the way we work and how develop the solutions for our clients. Our clients are mainly government-owned firm, but also private trading companies and wealthy private investors.

Our customers are mainly in Latin America, but the company is headquater is in Switzerland. We are opening offices in Panama and Caracas, this should be easaly be adabtable later.

Please have a look at our website www.vorelpartners.ch. In the brochure, we would segment our services in 1.) Project Developments 2.) Management Conulting 3.) Investment Management and 4.) Finance Solutions.

Also do have a look at www.vorelpartners.ch
(Click E for the English version)
Updates

I managed to put the Mock-Up to the Website.
It is actually not really a mock-up, it is a version I have designed myself.
Well as I am not a designer, I hope you can make it much better.
The content however is what I would put in any other design as well.

Target Market(s)

Top Management, Investors, Entrepreneurs, Government Officials

Industry/Entity Type

Management Consulting

Requirements
Must have
• Design should reflect this image elements:

We are entrepreneurs.
We are comitted to get things done.
We work closely with the client side by side.
We are a professional partner.
We are not afraid of delivering unconventional solutions.
We look at the problem from various angles.
We analyse, develop solutions and implent results.
Should not have
• Typical US-American style elements. We do not want to give the impression of being a US company.

We do not want to appear to be neo-liberal. We are a politically neutral professional consulting firm.

```html
<!DOCTYPE html>
<html lang="en">
<head>
<meta charset="utf-8">
<title>Vorel Partners – Brochure Cover</title>
<link rel="stylesheet" href="https://fonts.googleapis.com/css2?family=Open+Sans:wght@400;600;700&display=swap">
<style>
  :root {
    --page-bg: #ffffff;
    --paper: #ffffff;
    --brand-blue: #5a79bd;
    --deep-blue: #1f3f8f;
    --ink: #111111;
    --white: #ffffff;
    --fold: #a8a8a8;
    --photo-top: #7aa7de;
    --photo-mid: #3f86c0;
    --photo-bottom: #e4eaee;
  }
  * { margin: 0; padding: 0; box-sizing: border-box; }
  html, body {
    width: 1200px; height: 900px; overflow: hidden;
    background: var(--page-bg);
    font-family: "Open Sans", Arial, sans-serif;
  }
  .canvas { position: relative; width: 1200px; height: 900px; }

  .spread {
    position: absolute; left: 111px; top: 104px;
    width: 977px; height: 693px;
    background: var(--paper);
    box-shadow: 0 0 3px rgba(0,0,0,0.25);
  }

  .back-cover {
    position: absolute; left: 0; top: 134px;
    width: 488px; height: 559px;
    background: var(--brand-blue);
  }
  .contact {
    position: absolute; left: 47px; top: 356px;
    color: var(--white);
    font-size: 8.6px; font-weight: 600; line-height: 13px;
  }
  .contact p + p { margin-top: 9px; }
  .registration {
    position: absolute; left: 47px; top: 489px;
    color: var(--white);
    font-size: 10.4px; font-weight: 600; line-height: 16px;
    text-transform: uppercase;
  }

  .front-cover {
    position: absolute; left: 488px; top: 0;
    width: 489px; height: 693px;
  }
  .brand-name {
    position: absolute; right: 46px; top: 48px;
    font-size: 26px; font-weight: 600; letter-spacing: -0.2px;
    line-height: 1;
    color: var(--ink);
  }
  .blue-edge {
    position: absolute; left: 0; top: 134px;
    width: 489px; height: 5px;
    background: var(--brand-blue);
  }
  .cover-photo {
    position: absolute; left: 0; top: 139px;
    width: 489px; height: 554px;
    background: linear-gradient(180deg, var(--photo-top) 0%, var(--photo-mid) 55%, var(--photo-bottom) 100%);
  }
  .tagline {
    position: absolute; right: 46px; top: 139px;
    width: 198px; height: 35px;
    background: rgba(31,63,143,0.88);
    color: var(--white);
    font-size: 12.5px; font-weight: 600; letter-spacing: 0.4px;
    word-spacing: 3px;
    display: flex; align-items: center; justify-content: center;
    white-space: nowrap;
  }

  .fold-line { position: absolute; left: 598px; top: 80px; }
</style>
</head>
<body>
<div class="canvas">
  <div class="spread">
    <section class="back-cover">
      <div class="contact">
        <p>Vorel Partners AG<br>Lindenhof-Strasse 14<br>CH-8001 Zürich</p>
        <p>Tel. +41 44 512 38 20<br>Fax. +41 44 512 38 29</p>
        <p>info@vorelpartners.ch<br>www.vorelpartners.ch</p>
      </div>
      <p class="registration">Vorel Partners AG is registered as a<br>Swiss stock corporation since 1995.</p>
    </section>

    <section class="front-cover">
      <div class="brand-name">Vorel Partners</div>
      <div class="blue-edge"></div>
      <div class="cover-photo" role="img" aria-label="Photograph of a white terrace with lounge seating overlooking the sea under a blue sky"></div>
      <div class="tagline">ANALYZE DEVELOP DELIVER</div>
    </section>
  </div>

  <svg class="fold-line" width="2" height="740" aria-hidden="true">
    <line x1="1" y1="0" x2="1" y2="740" stroke="var(--fold)" stroke-width="1" stroke-dasharray="4 3"/>
  </svg>
</div>
</body>
</html>
```